Patient Fact sheets for medical conditions and treatments

Hi,

I need a new design for my patient fact sheets. I am moving from my current clinic and I am looking from a new look.

I have attached
1. a current Fact sheet
2. New home page to the website
3. New Logo.

They need to be single page and easily readable for patients.

The will be in both PDF and print form in the future.

Target Market(s)

Patients with chronic pain age 40+

Font styles to use
Serif

Requirements
Must have
• My logo, should be inline with design elements on the Front page provided.

Please use the same font as the Logo

```html
<!DOCTYPE html>
<html lang="en">
<head>
<meta charset="utf-8">
<title>PRP Therapy Fact Sheet</title>
<link href="https://fonts.googleapis.com/css2?family=Nunito+Sans:ital,wght@0,400;0,600;0,700;1,400&family=Roboto+Condensed:wght@700&display=swap" rel="stylesheet">
<style>
  :root {
    --purple: #33238a;
    --purple-text: #2e1f86;
    --ink: #2b2b2b;
    --grey-band: #c9c9cb;
    --grey-panel: #c8c8ca;
    --title-grey: #d9d9e2;
    --paper: #ffffff;
    --backdrop: #eeeeef;
  }
  * { margin: 0; padding: 0; box-sizing: border-box; }
  html, body { width: 1200px; height: 1200px; overflow: hidden; background: var(--backdrop); }
  body { position: relative; font-family: "Nunito Sans", Arial, sans-serif; color: var(--ink); }

  .sheet {
    position: absolute; left: 186px; top: 20px;
    width: 1020px; height: 1430px;
    background: var(--paper);
    transform: scale(0.8112); transform-origin: top left;
    box-shadow: 0 6px 22px rgba(0,0,0,.12);
    overflow: hidden;
  }
  .sheet-shapes { position: absolute; inset: 0; }
  .abs { position: absolute; }

  .brand { top: 52px; left: 520px; display: flex; align-items: center; gap: 14px; font-family: "Nunito Sans", Arial, sans-serif; font-weight: 600; color: #222; font-size: 27px; line-height: 32px; }
  .brand-mark { width: 14px; height: 14px; background: #222; flex: none; }

  .fact-label { left: 36px; top: 310px; font-size: 40px; color: #fff; letter-spacing: 2px; font-weight: 400; }

  .title { left: 462px; top: 168px; width: 540px; font-family: "Roboto Condensed", Arial, sans-serif; font-weight: 700; font-size: 41px; line-height: 38px; color: var(--title-grey); }
  .title-rule { left: 472px; top: 266px; width: 66px; height: 2px; background: #fff; }
  .intro-head { left: 483px; top: 297px; font-size: 20px; font-weight: 600; color: #e4e4ee; }
  .intro-body { left: 486px; top: 337px; width: 470px; font-size: 15.3px; line-height: 18.2px; color: #fff; text-align: center; }

  .section-head { font-size: 21px; font-weight: 700; color: var(--purple-text); letter-spacing: .2px; }
  .body-text { font-size: 15.3px; line-height: 18.1px; color: var(--ink); }

  .how-head { left: 36px; top: 470px; }
  .how-body { left: 37px; top: 514px; width: 440px; }
  .how-body p + p { margin-top: 18px; }

  .role-head { left: 533px; top: 581px; }
  .role-body { left: 534px; top: 624px; width: 435px; }
  .dot-list { list-style: none; }
  .dot-list li { position: relative; padding-left: 17px; }
  .dot-list li::before { content: ""; position: absolute; left: 0; top: 6px; width: 8px; height: 8px; border-radius: 50%; background: var(--purple); }
  .role-list { left: 534px; top: 698px; width: 420px; }
  .role-list li { margin-bottom: 6px; }

  .treat-head { left: 38px; top: 950px; }
  .treat-lead { left: 36px; top: 994px; font-weight: 600; }
  .treat-list-a { left: 38px; top: 1019px; }
  .treat-list-b { left: 355px; top: 1019px; }
  .treat-list-a li, .treat-list-b li { margin-bottom: 5.4px; padding-left: 22px; }
  .treat-rule { left: 308px; top: 1022px; width: 1.5px; height: 104px; background: var(--purple); }
  .treat-note { left: 38px; top: 1148px; width: 420px; }

  .results-head { left: 534px; top: 952px; }
  .results-body { left: 534px; top: 999px; width: 440px; }

  .disclaimer-head { left: 36px; top: 1232px; font-size: 13px; font-weight: 700; color: var(--purple-text); }
  .disclaimer-body { left: 37px; top: 1253px; width: 950px; font-size: 10.6px; line-height: 14.3px; color: #333; }

  .more-head { left: 36px; top: 1347px; font-size: 18px; font-weight: 700; color: var(--purple-text); }
  .web { left: 36px; top: 1374px; display: flex; align-items: center; gap: 12px; font-size: 22px; font-weight: 700; color: #222; }

  .contact { color: #fff; font-size: 15.5px; line-height: 20.5px; }
  .contact-address { left: 428px; top: 1350px; display: flex; gap: 8px; }
  .contact-rule { left: 746px; top: 1344px; width: 1.5px; height: 60px; background: rgba(255,255,255,.8); }
  .contact-lines { left: 795px; top: 1347px; }
  .contact-lines div { display: flex; align-items: center; gap: 8px; height: 25px; }
</style>
</head>
<body>
<main class="sheet">
  <svg class="sheet-shapes" viewBox="0 0 1020 1430" width="1020" height="1430">
    <defs>
      <linearGradient id="photoTone" x1="0" y1="0" x2="1" y2="1">
        <stop offset="0" stop-color="#eeeef0"/>
        <stop offset=".55" stop-color="#d3d3d7"/>
        <stop offset=".8" stop-color="#e8d97a"/>
        <stop offset="1" stop-color="#d7d7da"/>
      </linearGradient>
    </defs>
    <rect x="0" y="0" width="490" height="425" fill="url(#photoTone)" role="img" aria-label="Gloved hand holding two test tubes of separated plasma"/>
    <polygon points="370,0 1020,0 1020,136 437,136" fill="#ffffff"/>
    <polygon points="0,425 478,425 517,511 1020,511 1020,521 510,521 470,445 0,445" fill="var(--grey-band)"/>
    <polygon points="345,136 1020,136 1020,511 517,511" fill="var(--purple)"/>
    <rect x="0" y="923" width="1020" height="292" fill="var(--grey-panel)"/>
    <polygon points="335,1325 1020,1325 1020,1335 340,1335" fill="var(--grey-band)"/>
    <polygon points="0,1375 358,1375 372,1402 0,1402" fill="#d4d4d6"/>
    <polygon points="345,1335 1020,1335 1020,1430 395,1430" fill="var(--purple)"/>
  </svg>

  <div class="abs brand">
    <span class="brand-mark"></span>
    <div class="brand-name">Dr Alan Reeve<br>Harbour Spine Care</div>
  </div>

  <div class="abs fact-label">FACT SHEET</div>

  <h1 class="abs title">PLATELET RICH PLASMA (PRP) THERAPY</h1>
  <div class="abs title-rule"></div>
  <h2 class="abs intro-head">WHAT IS PRP?</h2>
  <p class="abs intro-body">Platelet-Rich Plasma (PRP) is concentrated platelets and white blood cells derived from your own blood. Platelet Rich Plasma Injection Therapy (PRP therapy), is a growing treatment approach for soft tissue injuries including tendon, muscle and ligaments. It is also showing good results for mild to moderate osteoarthritis. While this approach has been used overseas for many years, it’s fairly new to Australia in the treatment of musculoskeletal and orthopaedic conditions.</p>

  <h2 class="abs section-head how-head">HOW DOES PRP WORK?</h2>
  <div class="abs body-text how-body">
    <p>Some tissues in the body have a poor blood supply or respond poorly to excessive load, ultimately failing to heal naturally. While some of our primary treatment such as physiotherapy, massage, biomechanical correction and other forms of treatment are used to treat these soft tissue injuries, sometimes the body fails to respond.</p>
    <p>PRP therapy utilises the healing properties in blood to allow a healing reaction to occur in a tissue that’s not healing on its own. Our blood has small granules called ‘platelets’, which contain special growth factors that when released, allow stem cells in the particular tissue to ‘switch’ on and cause new tissue to be created and heal the injured area. HOW DOES PRP WORK? Take the example of achilles tendinopathy. If the achilles is painful, thickened and not responding to rehabilitation, then the sports physician will inject the PRP into the achilles which will cause the tendon cells (tenocytes/ fibroblasts) to create new achilles collagen to strengthen the achilles. White blood cells also enter the area to mop up any achilles tissue that may have been damaged due to the ongoing pain and thickening in the area.</p>
  </div>

  <h2 class="abs section-head role-head">ROLE OF PLATELETS &amp; GROWTH FACTORS</h2>
  <p class="abs body-text role-body">PRP contains highly concentrated platelets. Platelets have been identified to secrete growth factors, which are known to play a role in:</p>
  <ul class="abs body-text dot-list role-list">
    <li>Increasing tissue vascularity and increasing the rate of epithelial tissue production <em>(wound healing)</em></li>
    <li>Attracting other cells that fight infection</li>
    <li>Acting as a seal during closures</li>
    <li>Providing an immediate surgical hemostatic agent <em>(reduction of bleeding)</em></li>
    <li>Osteogenesis <em>(bone regeneration and repair)</em></li>
  </ul>

  <h2 class="abs section-head treat-head">WHAT CAN PRP TREAT?</h2>
  <p class="abs body-text treat-lead">PRP therapy can be used for:</p>
  <ul class="abs body-text dot-list treat-list-a">
    <li>Orthopedic surgery</li>
    <li>Cardiac surgery</li>
    <li>Plastic and cosmetic surgery</li>
    <li>Ear, nose, throat (ent) surgery</li>
    <li>Oral maxillofacial surgery</li>
  </ul>
  <div class="abs treat-rule"></div>
  <ul class="abs body-text dot-list treat-list-b">
    <li>Neurosurgery</li>
    <li>Vascular surgery</li>
    <li>Wound healing</li>
    <li>Burn care</li>
  </ul>
  <p class="abs body-text treat-note">Ask your doctor whether plateletrich plasma is appropriate for your surgical procedure</p>

  <h2 class="abs section-head results-head">WHAT ARE THE EXPECTED RESULTS OF PRP?</h2>
  <p class="abs body-text results-body">Because the goal of PRP therapy is to resolve pain through healing, it could prove to have lasting results. Initial improvement may be seen within a few weeks, gradually increasing as the healing progresses. Research studies and clinical practice have shown PRP therapy to be very effective at relieving pain and returning patients to their normal lives. The need for surgery can also be greatly reduced by treating injured tissues before the damage progresses and the condition is irreversible.</p>

  <h3 class="abs disclaimer-head">DISCLAIMER</h3>
  <p class="abs disclaimer-body">Please note the contents contained in this Patient Fact Sheet are not intended as a substitute for your own independent health professional’s advice, diagnosis or treatment. At Eastfield Pain Clinic, we assess every patient’s condition individually. As leaders in pain intervention, we aim to provide advanced, innovative, and evidence-based treatments tailored to suit each patient. As such, recommended treatments and their outcomes will vary from patient to patient. If you would like to find out whether our treatments are suitable for your specific condition, please speak to one of our doctors at the time of your consultation.</p>

  <h3 class="abs more-head">FOR MORE INFORMATION</h3>
  <div class="abs web">
    <svg width="20" height="20" viewBox="0 0 20 20" aria-hidden="true"><g fill="none" stroke="var(--purple)" stroke-width="1.8"><circle cx="10" cy="10" r="8.5"/><ellipse cx="10" cy="10" rx="3.8" ry="8.5"/><path d="M1.5 10h17M3 5.5h14M3 14.5h14"/></g></svg>
    <span>eastfieldpain.com.au</span>
  </div>

  <div class="abs contact contact-address">
    <svg width="16" height="20" viewBox="0 0 16 20" aria-hidden="true"><path d="M8 1a6.5 6.5 0 0 0-6.5 6.5C1.5 12 8 19 8 19s6.5-7 6.5-11.5A6.5 6.5 0 0 0 8 1z" fill="none" stroke="#fff" stroke-width="1.6"/><circle cx="8" cy="7.5" r="2.3" fill="#fff"/></svg>
    <div>Eastfield Pain Clinic<br>Wattle House, Ground Floor<br>48 Linden Road, Lindale VIC 3999</div>
  </div>
  <div class="abs contact-rule"></div>
  <div class="abs contact contact-lines">
    <div><svg width="16" height="16" viewBox="0 0 16 16" aria-hidden="true"><circle cx="8" cy="8" r="8" fill="#fff"/><path d="M5 4.2l1.4-.3 1 2.2-.9.8a6 6 0 0 0 2.6 2.6l.8-.9 2.2 1-.3 1.4c-3.5.4-7.2-3.3-6.8-6.8z" fill="var(--purple)"/></svg><span>03 9000 1234</span></div>
    <div><svg width="16" height="16" viewBox="0 0 16 16" aria-hidden="true"><rect x="1" y="6" width="14" height="9" rx="1" fill="#fff"/><rect x="4" y="1" width="8" height="6" fill="#fff"/><rect x="4" y="9" width="8" height="1.5" fill="var(--purple)"/><rect x="4" y="11.5" width="8" height="1.5" fill="var(--purple)"/></svg><span>03 9000 1235</span></div>
    <div><svg width="16" height="12" viewBox="0 0 16 12" aria-hidden="true"><rect width="16" height="12" rx="1.5" fill="#fff"/><path d="M1 1.5l7 5.5 7-5.5" fill="none" stroke="var(--purple)" stroke-width="1.4"/></svg><span>hello@eastfieldpain.com.au</span></div>
  </div>
</main>
</body>
</html>
```